Permanent Makeup Certificate for Lash Crest Institute Certified Artists

I need a beautifully designed certificate for my students who have successfully obtained my certification for Eyebrow Micropigmentation.

I have attached my sample certificate in InDesign format. This certificate is how I want the Certified Artist Certificate to read. My wording is extremely important for US Insurance reasons. I would like it to be in 11 x 17 inch format for USA printing.

I have also attached samples of certificates from other companies to give you an idea of how fancy I would like it to be. My company colors are pink and white, so I would like the dominant colors to be shades of pink and white. I like pink pastel combines with darker shades of pink and white. If the design calls for another color in addition to pink, that would also be great. I really like the colors in the Vexora Certificate.

I have attached a copy of my signature in .png

Target Market(s)

Beauty Industry

Industry/Entity Type

Artists

Font styles to use
Serif
Script

Colors
ffffff
f9d9e8
9bcb3c
cadf82
e667a6
e34297
eea4c8
b7a5cd

Requirements
Must have
• Wording exactly as I uploaded in InDesign file
Nice to have
• Beautiful images of female face, I am not sure if I like this idea. Just an experiement

```html
<!DOCTYPE html>
<html lang="en">
<head>
<meta charset="utf-8">
<title>Certificate of Excellence – Lash Crest Institute</title>
<link href="https://fonts.googleapis.com/css2?family=Pinyon+Script&family=Ubuntu:wght@400;500;700&display=swap" rel="stylesheet">
<style>
  :root {
    --page-bg: #f2f2f2;
    --paper: #ffffff;
    --pink-pastel: #f9d9e8;
    --pink-soft: #eea4c8;
    --pink-mid: #e667a6;
    --pink-deep: #e34297;
    --plum: #7a2a68;
    --ink: #3c3c3c;
    --ink-soft: #5a5a5a;
  }
  * { box-sizing: border-box; margin: 0; padding: 0; }
  html, body { width: 1200px; height: 978px; overflow: hidden; background: var(--page-bg); }
  body { position: relative; font-family: "Ubuntu", sans-serif; color: var(--ink); }

  .certificate {
    position: absolute; left: 20px; top: 113px;
    width: 1160px; height: 751px;
    background: var(--paper);
    overflow: hidden;
    box-shadow: 0 2px 10px rgba(0,0,0,.15);
  }

  .portrait-panel {
    position: absolute; left: 520px; top: 0; width: 640px; height: 100%;
    background:
      linear-gradient(to right, #ffffff 0%, rgba(255,255,255,0.6) 18%, rgba(255,255,255,0) 40%),
      radial-gradient(ellipse at 72% 42%, #f3c1a6 0%, rgba(243,193,166,0) 38%),
      radial-gradient(ellipse at 45% 85%, var(--pink-mid) 0%, rgba(230,103,166,0) 45%),
      radial-gradient(ellipse at 30% 10%, var(--pink-soft) 0%, rgba(238,164,200,0) 40%),
      linear-gradient(to bottom, #f6d3e2, #f1b6cf);
  }

  .border-ornament {
    position: absolute;
    background: linear-gradient(135deg, rgba(238,164,200,0.35), rgba(249,217,232,0.15));
    border-radius: 40px;
  }
  .border-ornament.top { left: 32px; top: 40px; width: 260px; height: 60px; }
  .border-ornament.bottom { left: 32px; top: 650px; width: 260px; height: 60px; }

  .frame-line { position: absolute; background: var(--pink-mid); }
  .frame-line.left { left: 76px; top: 110px; width: 2px; height: 540px; }
  .frame-line.top { left: 290px; top: 78px; width: 160px; height: 2px; }
  .frame-line.bottom { left: 290px; top: 684px; width: 160px; height: 2px; }

  .content { position: absolute; left: 0; top: 0; width: 790px; height: 100%; }
  .centered { position: absolute; left: 0; width: 790px; text-align: center; }

  .brand {
    top: 150px; font-family: "Ubuntu", sans-serif; font-weight: 500;
    font-size: 34px; color: var(--plum); letter-spacing: 0.5px;
    display: flex; justify-content: center; align-items: center; gap: 12px;
  }
  .brand-dot { width: 14px; height: 14px; border-radius: 50%; background: var(--plum); }

  .title { top: 268px; font-family: "Pinyon Script", cursive; font-size: 48px; color: var(--ink-soft); }
  .certify { top: 336px; font-size: 13px; letter-spacing: 0.6px; color: var(--ink-soft); }
  .recipient { top: 390px; font-family: "Pinyon Script", cursive; font-size: 38px; color: var(--ink); }

  .name-rule { position: absolute; left: 147px; top: 440px; width: 490px; height: 14px; }

  .statement { top: 484px; font-size: 14px; line-height: 18px; color: var(--ink-soft); }
  .statement strong { font-weight: 700; color: var(--ink); }

  .date-block { position: absolute; left: 200px; top: 596px; width: 110px; text-align: center; }
  .date-value { font-size: 14px; color: var(--ink); padding-bottom: 4px; border-bottom: 1px solid #9a9a9a; }
  .date-label { font-size: 9px; margin-top: 6px; color: var(--ink-soft); }

  .signature-block { position: absolute; left: 468px; top: 588px; width: 200px; text-align: center; }
  .signature { font-family: "Pinyon Script", cursive; font-size: 26px; color: #222; border-bottom: 1px solid #9a9a9a; line-height: 34px; }
  .signer-name { font-size: 9px; font-weight: 700; margin-top: 4px; color: var(--ink); }
  .signer-role { font-size: 9px; color: var(--ink-soft); line-height: 12px; }
</style>
</head>
<body>
  <main class="certificate">
    <div class="portrait-panel" role="img" aria-label="Beauty photograph of a woman with pink orchids and soft pink makeup"></div>

    <div class="border-ornament top" role="img" aria-label="Pink decorative scroll corner"></div>
    <div class="border-ornament bottom" role="img" aria-label="Pink decorative scroll corner"></div>
    <div class="frame-line left"></div>
    <div class="frame-line top"></div>
    <div class="frame-line bottom"></div>

    <section class="content">
      <div class="centered brand"><span class="brand-dot"></span>Lash Crest Institute</div>
      <h1 class="centered title">Certificate of Excellence</h1>
      <p class="centered certify">THIS IS TO CERTIFY THAT</p>
      <p class="centered recipient">John Noname Doe</p>

      <svg class="name-rule" viewBox="0 0 490 14" aria-hidden="true">
        <line x1="6" y1="7" x2="484" y2="7" stroke="#6a6a6a" stroke-width="1.2"/>
        <circle cx="6" cy="7" r="3" fill="none" stroke="#6a6a6a"/>
        <circle cx="484" cy="7" r="3" fill="none" stroke="#6a6a6a"/>
        <circle cx="239" cy="10" r="1" fill="#6a6a6a"/>
        <circle cx="245" cy="10" r="1" fill="#6a6a6a"/>
        <circle cx="251" cy="10" r="1" fill="#6a6a6a"/>
      </svg>

      <p class="centered statement">
        Has successfully proven to be an<br>
        Artist of the Highest Standard in Eyebrow Micropigmentation<br>
        using the <strong>LASH CREST INTERNATIONAL</strong>® Microblading Method
      </p>

      <div class="date-block">
        <div class="date-value">23.07.2016</div>
        <div class="date-label">Date</div>
      </div>

      <div class="signature-block">
        <div class="signature">Maren Elise Toller</div>
        <div class="signer-name">Maren Elise Toller</div>
        <div class="signer-role">Master Instructor</div>
        <div class="signer-role">Lash Crest International®</div>
      </div>
    </section>
  </main>
</body>
</html>
```